Print materials for 3-star hotel

We are changing up our print materials (notepads, letterheads, key card jackets, small flyer for the room rates) We are a 3 star business hotel in the Philippines and have mainly used grey tones and clean, simple lines. See attached photos for logo and hotel interior photos.

Target Market(s)

Business

Contact Information for Business Card

Corvale Terrace Hotel
Lindwell Banca Avenue corner Tolenta St Cebu City 6000 Philippines
Tel: +63 32 481 7302
Mobile: +63 917 648 2095
www.corvaleterracehotel.example

Font styles to use
Serif
Sans Serif

Requirements
Must have
• Simple
• Readable font and font size
Nice to have
• Neutral colors, grey and taupes
Should not have
• No purples and bright blues

```html
<!DOCTYPE html>
<html lang="en">
<head>
<meta charset="utf-8">
<title>Corvale Terrace Hotel – Business Card</title>
<link rel="stylesheet" href="https://fonts.googleapis.com/css2?family=Cinzel:wght@400&family=Roboto:wght@400;500&display=swap">
<style>
  :root {
    --backdrop: #dedede;
    --card: #b6a68a;
    --card-shadow: rgba(0, 0, 0, 0.35);
    --ink: #f7f2e9;
    --mark-faint: rgba(255, 255, 255, 0.12);
  }
  * { margin: 0; padding: 0; box-sizing: border-box; }
  html, body {
    width: 1200px; height: 960px; overflow: hidden;
    background: var(--backdrop);
  }
  .canvas { position: relative; width: 1200px; height: 960px; }

  .card {
    position: absolute;
    width: 601px; height: 343px;
    background: var(--card);
    box-shadow: 1px 2px 3px var(--card-shadow);
    color: var(--ink);
    font-family: "Roboto", Arial, sans-serif;
  }
  .card-front { left: 314px; top: 113px; }
  .card-back  { left: 311px; top: 472px; }

  /* brand block */
  .brand {
    position: absolute; right: 38px; top: 40px;
    width: 230px; text-align: center;
    font-family: "Cinzel", Georgia, serif; font-weight: 400;
    color: var(--ink);
  }
  .brand-square {
    display: block; width: 50px; height: 50px;
    margin: 0 auto 10px; background: var(--ink);
  }
  .brand-name { font-size: 16px; letter-spacing: 2.6px; line-height: 18px; }
  .brand-sub  { font-size: 12px; letter-spacing: 4px; line-height: 16px; }

  /* person */
  .person { position: absolute; left: 36px; top: 166px; }
  .person-name {
    font-family: "Cinzel", Georgia, serif; font-weight: 400;
    font-size: 23px; line-height: 28px;
  }
  .person-title { font-size: 14px; font-weight: 500; line-height: 18px; }

  .divider {
    position: absolute; left: 36px; right: 37px; top: 224px;
    height: 1px; background: var(--ink);
  }

  .contact-list {
    position: absolute; left: 37px; top: 239px;
    list-style: none; font-size: 14px; line-height: 19px;
  }
  .contact-list li { display: flex; align-items: center; gap: 8px; }
  .contact-list svg { width: 14px; height: 14px; fill: var(--ink); flex: none; }

  .address {
    position: absolute; right: 36px; top: 259px;
    text-align: right; font-size: 14px; line-height: 19px; font-style: normal;
  }

  /* back */
  .back-mark {
    position: absolute; left: 20px; top: 21px;
    width: 315px; height: 300px; background: var(--mark-faint);
  }
  .back-web {
    position: absolute; right: 38px; top: 289px;
    font-size: 14px; letter-spacing: 2.8px;
  }
</style>
</head>
<body>
<main class="canvas">

  <section class="card card-front" aria-label="Business card front">
    <div class="brand">
      <span class="brand-square" aria-hidden="true"></span>
      <div class="brand-name">Corvale Terrace</div>
      <div class="brand-sub">Hotel</div>
    </div>

    <div class="person">
      <h1 class="person-name">DANIEL ARCEO</h1>
      <p class="person-title">CEO/Founder</p>
    </div>

    <div class="divider"></div>

    <ul class="contact-list">
      <li>
        <svg viewBox="0 0 16 16" aria-hidden="true"><path d="M3.6 1.5l2.2 2.6-1.3 1.6c.9 2 2.5 3.6 4.4 4.6l1.6-1.3 2.6 2.2-1.3 2.3C6.6 13.3 2.2 8.9 1.5 3z"/></svg>
        +63 32 481 7302
      </li>
      <li>
        <svg viewBox="0 0 16 16" aria-hidden="true"><path d="M4.5 1h7v14h-7zM6 3v9h4V3zm1.5 10.2h1v1h-1z" fill-rule="evenodd"/></svg>
        +63 917 648 2095
      </li>
      <li>
        <svg viewBox="0 0 16 16" aria-hidden="true"><path d="M4 1h8v4H4zM1 6h14v6h-3v3H4v-3H1zm4 4v3h6v-3z" fill-rule="evenodd"/></svg>
        +63 32 481 7310
      </li>
      <li>
        <svg viewBox="0 0 16 16" aria-hidden="true"><path d="M1.5 4h13v8.5h-13zM2.5 4.5L8 9l5.5-4.5v1.3L8 10.2 2.5 5.8z" fill-rule="evenodd"/></svg>
        daniel@corvaleterrace.example
      </li>
    </ul>

    <address class="address">
      Lindwell Banca Ave cor. Tolenta St<br>
      Cebu City 6000 Philippines<br>
      www.corvaleterracehotel.example
    </address>
  </section>

  <section class="card card-back" aria-label="Business card back">
    <div class="back-mark" aria-hidden="true"></div>
    <p class="back-web">www.corvaleterracehotel.example</p>
  </section>

</main>
</body>
</html>
```